Harrowgate Care Assurance Ltd needs a business card and logo

We need a logo for documents, invoices etc and a business card to match. We are a health auditing, training and consulting company based in NZ and working in both Australia and NZ. We ensure health organisations meet all their compliance requirements and develop expertise in the health auditing sector. The design should in some way reflect either symbols for quality management in the health sector.

Target Market(s)

Health providers and those wishing to increase their capability in meeting and understanding compliance requirements

Industry/Entity Type

Business

Contact Information for Business Card

Logo plus contact details

Logo Text

Health auditing, consultancy and training

Requirements
Must have
• Name and contact details director: Marla Fenwick, mfenwick@hca-example.co.nz, PO Box 318, Warkworth, NZ, cell +6427391652

```html
<!DOCTYPE html>
<html lang="en">
<head>
<meta charset="utf-8">
<title>Harrowgate Care Assurance Ltd — Business Card</title>
<link href="https://fonts.googleapis.com/css2?family=Open+Sans:wght@400;600;700&display=swap" rel="stylesheet">
<style>
  :root {
    --backdrop: #222222;
    --blue-light: #1a82cf;
    --blue-deep: #0a5b9e;
    --blue-band: #2179c3;
    --ink: #333333;
    --charcoal: #333333;
    --white: #ffffff;
  }
  * { margin: 0; padding: 0; box-sizing: border-box; }
  html, body { width: 1200px; height: 1001px; overflow: hidden; }
  body { background: var(--backdrop); font-family: "Open Sans", Arial, sans-serif; position: relative; }

  .card {
    position: absolute;
    left: 276px;
    width: 618px;
    height: 380px;
    border-radius: 14px;
    overflow: hidden;
  }
  .card--front {
    top: 99px;
    background: radial-gradient(ellipse 60% 65% at 45% 48%, var(--blue-light) 0%, var(--blue-deep) 100%);
  }
  .card--back { top: 511px; background: var(--white); }

  .brand-mark {
    position: absolute;
    border-radius: 50%;
    width: 112px;
    height: 112px;
  }
  .card--front .brand-mark { left: 139px; top: 138px; background: radial-gradient(circle at 40% 35%, #ffffff 55%, #dcdfe3 100%); }
  .card--back .brand-mark { left: 45px; top: 64px; background: radial-gradient(circle at 40% 30%, #2a9be0 0%, #0c63ae 100%); }

  .brand-name {
    position: absolute;
    font-weight: 400;
    white-space: nowrap;
    line-height: 1;
  }
  .brand-name__line1 { display: block; font-size: 24px; letter-spacing: 1px; }
  .brand-name__line2 { display: block; font-size: 14px; letter-spacing: 4.6px; margin-top: 5px; padding-left: 29px; }
  .card--front .brand-name { left: 256px; top: 176px; color: var(--white); }
  .card--back .brand-name { left: 163px; top: 102px; color: var(--ink); }

  .wave { position: absolute; inset: 0; width: 100%; height: 100%; }

  .contact {
    position: absolute;
    right: 50px;
    top: 230px;
    text-align: right;
    color: var(--white);
    font-size: 15.5px;
    line-height: 1;
  }
  .contact__name { font-weight: 700; font-size: 16.5px; letter-spacing: 1px; margin-bottom: 13px; }
  .contact__address { margin-bottom: 14px; }
  .contact__row { display: flex; justify-content: flex-end; align-items: center; gap: 10px; margin-bottom: 6px; }
  .contact__icon { width: 14px; height: 14px; flex: none; }
</style>
</head>
<body>
  <section class="card card--front" aria-label="Card front">
    <div class="brand-mark"></div>
    <div class="brand-name">
      <span class="brand-name__line1">HARROWGATE CARE</span>
      <span class="brand-name__line2">ASSURANCE LTD</span>
    </div>
  </section>

  <section class="card card--back" aria-label="Card back">
    <svg class="wave" viewBox="0 0 747 457" preserveAspectRatio="none" aria-hidden="true">
      <path fill="var(--charcoal)" d="M0,358 C120,385 250,350 340,296 C270,350 140,405 0,388 Z"/>
      <path fill="var(--blue-band)" d="M0,402 C150,438 300,380 420,300 C530,228 620,200 718,205 C620,210 540,240 445,302 C320,392 180,452 0,425 Z"/>
      <path fill="var(--blue-band)" d="M55,457 C250,452 380,340 500,272 C600,228 680,222 747,232 L747,457 Z"/>
    </svg>
    <div class="contact">
      <p class="contact__name">MARLA FENWICK</p>
      <p class="contact__address">PO Box 318, Warkworth, NZ</p>
      <p class="contact__row">+6427391652
        <svg class="contact__icon" viewBox="0 0 14 14" aria-hidden="true"><rect x="3.5" y="1" width="7" height="12" rx="1.2" fill="none" stroke="#fff" stroke-width="1.4"/><rect x="5.5" y="10.5" width="3" height="1" fill="#fff"/></svg>
      </p>
      <p class="contact__row">mfenwick@hca-example.co.nz
        <svg class="contact__icon" viewBox="0 0 14 14" aria-hidden="true"><rect x="1" y="3" width="12" height="8.5" fill="#fff"/><path d="M1,3 L7,8 L13,3" fill="none" stroke="#2179c3" stroke-width="1.2"/></svg>
      </p>
    </div>
    <div class="brand-mark"></div>
    <div class="brand-name">
      <span class="brand-name__line1">HARROWGATE CARE</span>
      <span class="brand-name__line2">ASSURANCE LTD</span>
    </div>
  </section>
</body>
</html>
```